Catering Menu Package

I currently have a complete menu package, which we have redesigned as far as content, now I need to it put together in a catalog type format. It is essentially 10-12 pages in length, and will be sent for print production. Upon receiving a final edit
Updates

I have added an example gif to the project.

I did this free hand this basically what I am looking for. please change text and type to whatever you think would look best. This is a total rough design so, feel free to change any and everything. The text for the page is on the word documents. If you need more images let me know I am in the process of getting as many images uploaded for your use.

Project Deadline Extended
Reason: I figured we got a late jump with questions, so i am extending a few days .

Target Market(s)

The target market is business who wish to have catered luncheons, breakfasts , meetings

Industry/Entity Type

Catering

Requirements
Must have
• I have attached a copy of the text that what we want in the package, our logo, and i have also attached a catering package of another company to give you an idea what the finished product will be
Should not have
• It should not look identical to the example catering packages, these are for some inspiration we want our own design with the same type of look and feel

```html
<!DOCTYPE html>
<html lang="en">
<head>
<meta charset="utf-8">
<title>Harbor Field Caterers – Sides &amp; Soups Menu</title>
<link href="https://fonts.googleapis.com/css2?family=Lobster+Two:ital@1&family=Crimson+Text:ital,wght@0,400;0,600;0,700;1,400&display=swap" rel="stylesheet">
<style>
  :root{
    --backdrop:#6f4d31;
    --paper:#ece5d7;
    --orange:#f07a22;
    --orange-deep:#e8691a;
    --ink:#1c1a17;
    --green:#5cb85a;
    --white:#ffffff;
  }
  *{box-sizing:border-box;margin:0;padding:0}
  html,body{width:1200px;height:800px;overflow:hidden}
  body{background:var(--backdrop);position:relative;font-family:"Crimson Text",Georgia,serif;color:var(--ink)}
  .page{position:absolute;top:16px;width:566px;height:746px;background:var(--paper);overflow:hidden}
  .page--front{left:22px}
  .page--back{left:608px}
  .page__art{position:absolute;left:0;top:0}
  .abs{position:absolute}
  .dish{position:absolute;font-family:"Lobster Two",Georgia,cursive;font-style:italic;color:var(--orange);font-size:17px;line-height:1;white-space:nowrap;letter-spacing:.2px}
  .price{position:absolute;font-weight:600;font-size:19px;line-height:1;color:var(--ink)}
  .desc{position:absolute;font-size:12px;line-height:15.5px;color:var(--ink)}
  .section-title{position:absolute;font-family:"Lobster Two",Georgia,cursive;font-style:italic;color:var(--orange);font-size:31px;line-height:1;white-space:nowrap}
  .section-note{position:absolute;font-size:15px;line-height:1;white-space:nowrap}
  .section-rule{position:absolute;height:4px;background:var(--orange)}
  .section-badge{position:absolute;background:var(--orange-deep);color:var(--white);font-family:"Lobster Two",Georgia,cursive;font-style:italic;font-size:26px;line-height:40px;text-align:center;white-space:nowrap}
  .terms{position:absolute;left:12px;top:656px;width:398px;height:29px;background:var(--green);border-radius:9px;color:var(--white);font-size:10px;line-height:12.5px;text-align:center;padding-top:2px}
  .contact{position:absolute;left:0;top:689px;width:430px;height:57px;background:var(--orange)}
  .contact__call{position:absolute;left:20px;top:4px;color:var(--white);font-style:italic;font-size:10px;letter-spacing:.2px}
  .contact__phone{position:absolute;left:30px;top:17px;display:flex;align-items:center;gap:8px;color:var(--ink);font-style:italic;font-weight:600;font-size:22px}
  .contact__address{position:absolute;left:240px;top:5px;color:var(--white);font-size:10.5px;line-height:14px}
  .brand{position:absolute;top:519px;width:132px;height:227px;background:var(--white);display:flex;flex-direction:column;align-items:center;justify-content:center;gap:14px}
  .brand__dot{width:70px;height:70px;border-radius:50%;background:var(--orange)}
  .brand__name{font-weight:700;font-size:20px;line-height:22px;text-align:center;color:var(--ink)}
</style>
</head>
<body>

<!-- FRONT PAGE -->
<section class="page page--front">
  <svg class="page__art" width="566" height="746" viewBox="0 0 566 746">
    <defs>
      <linearGradient id="pastaTone" x1="0" y1="0" x2="1" y2="1">
        <stop offset="0" stop-color="#7d8f3e"/>
        <stop offset=".35" stop-color="#e7b765"/>
        <stop offset=".7" stop-color="#d9652a"/>
        <stop offset="1" stop-color="#efd9a2"/>
      </linearGradient>
    </defs>
    <path role="img" aria-label="Photo of pasta salad with penne, zucchini and tomatoes" d="M468,0 C446,150 440,360 418,519 L566,519 L566,0 Z" fill="url(#pastaTone)"/>
  </svg>

  <div class="dish" style="left:18px;top:12px">Roman Salad</div>
  <p class="desc" style="left:18px;top:31px;width:420px">Crisp Romaine Lettuce, Black Olives, Grape Tomatoes, Feta Cheese, and Red Onions. Served with our Chef-made Parmesan-Pepper Dressing.</p>
  <div class="price" style="left:336px;top:65px">$&amp;.&amp;&amp;</div>

  <div class="dish" style="left:18px;top:84px">Farm Fresh Garden Salad</div>
  <p class="desc" style="left:18px;top:104px;width:430px">Spring Mix, Shredded Carrots, Grape Tomatoes, Cucumbers, Red Onions, and Garlic Croutons. Accompanied with Ranch Dressing and our Chef-made Balsamic Dressing.</p>
  <div class="price" style="left:336px;top:135px">$&amp;.&amp;&amp;</div>

  <h2 class="section-title" style="left:74px;top:178px">Vegetable Substitutes</h2>
  <p class="section-note" style="left:68px;top:218px">To substitute, free of charge, to add $&amp;.&amp;&amp;</p>

  <div class="dish" style="left:18px;top:255px">Lemon Scented Petit Green Beans</div><div class="price" style="left:336px;top:254px">$&amp;.&amp;&amp;</div>
  <div class="dish" style="left:18px;top:285px">Tomato-Zucchini Casserole</div><div class="price" style="left:336px;top:284px">$&amp;.&amp;&amp;</div>
  <div class="dish" style="left:18px;top:319px">Steamed Broccoli</div><div class="price" style="left:334px;top:318px">$&amp;.&amp;&amp;</div>
  <div class="dish" style="left:18px;top:350px">Maple Glazed Carrots</div><div class="price" style="left:334px;top:349px">$&amp;.&amp;&amp;</div>
  <div class="dish" style="left:18px;top:379px">Sautéed Local Corn</div><div class="price" style="left:334px;top:378px">$&amp;.&amp;&amp;</div>

  <div class="section-rule" style="left:0;top:435px;width:445px"></div>
  <h2 class="section-badge" style="left:128px;top:416px;width:208px">Ala Carte Sides</h2>

  <div class="dish" style="left:22px;top:474px">Lemon Scented Petit Green Beans</div><div class="price" style="left:338px;top:473px">$&amp;.&amp;&amp;</div>
  <div class="dish" style="left:22px;top:504px">Tomato-Zucchini Casserole</div><div class="price" style="left:338px;top:503px">$&amp;.&amp;&amp;</div>
  <div class="dish" style="left:22px;top:538px">Steamed Broccoli</div><div class="price" style="left:338px;top:537px">$&amp;.&amp;&amp;</div>
  <div class="dish" style="left:22px;top:569px">Maple Glazed Carrots</div><div class="price" style="left:338px;top:568px">$&amp;.&amp;&amp;</div>
  <div class="dish" style="left:22px;top:598px">Sautéed Local Corn</div><div class="price" style="left:338px;top:597px">$&amp;.&amp;&amp;</div>
  <div class="dish" style="left:22px;top:625px">Pasta Vegetable Salad</div><div class="price" style="left:338px;top:624px">$&amp;.&amp;&amp;</div>

  <p class="terms">All Prices are per Person, with a 10 person minimum order per item chosen.<br>Local Products used when available and in season</p>

  <footer class="contact">
    <span class="contact__call">CALL OR EMAIL US TODAY:</span>
    <span class="contact__phone">
      <svg width="24" height="20" viewBox="0 0 24 20" aria-hidden="true"><path d="M2,7 C2,2 22,2 22,7 L22,9 L17,9 L17,6 L7,6 L7,9 L2,9 Z M6,10 L18,10 L21,18 L3,18 Z" fill="#1c1a17"/><circle cx="12" cy="14" r="2.2" fill="#f07a22"/></svg>
      410-555-0148
    </span>
    <address class="contact__address" style="font-style:normal">214 Orchard Way<br>Millbrook, MD 20999<br>www.harborfieldcaterers.com</address>
  </footer>

  <div class="brand" style="left:434px">
    <span class="brand__dot"></span>
    <span class="brand__name">Harbor Field<br>Caterers</span>
  </div>
</section>

<!-- BACK PAGE -->
<section class="page page--back">
  <svg class="page__art" width="566" height="746" viewBox="0 0 566 746">
    <defs>
      <linearGradient id="soupTone" x1="0" y1="0" x2="0" y2="1">
        <stop offset="0" stop-color="#c9b8a4"/>
        <stop offset=".3" stop-color="#d2572a"/>
        <stop offset=".7" stop-color="#c9421f"/>
        <stop offset="1" stop-color="#e9e4df"/>
      </linearGradient>
    </defs>
    <path role="img" aria-label="Photo of a bowl of tomato soup" d="M436,0 C470,150 482,360 440,519 L566,519 L566,0 Z" fill="url(#soupTone)"/>
  </svg>

  <div class="dish" style="left:24px;top:14px">Country Potato Salad</div><div class="price" style="left:336px;top:13px">$&amp;.&amp;&amp;</div>
  <div class="dish" style="left:24px;top:40px">Asparagus and Petit Green Bean Salad</div><div class="price" style="left:336px;top:59px">$&amp;.&amp;&amp;</div>
  <div class="dish" style="left:24px;top:85px">Oven Roasted Redskin Potatoes</div><div class="price" style="left:336px;top:84px">$&amp;.&amp;&amp;</div>
  <div class="dish" style="left:24px;top:116px">Balsamic Roasted Seasonal Vegetable Medley</div><div class="price" style="left:336px;top:135px">$&amp;.&amp;&amp;</div>
  <div class="dish" style="left:24px;top:161px">Creamy Cole Slaw</div><div class="price" style="left:336px;top:160px">$&amp;.&amp;&amp;</div>
  <div class="dish" style="left:24px;top:194px">Caprese Salad</div><div class="price" style="left:336px;top:193px">$&amp;.&amp;&amp;</div>
  <div class="dish" style="left:26px;top:226px">Jeweled Rice</div><div class="price" style="left:336px;top:225px">$&amp;.&amp;&amp;</div>
  <div class="dish" style="left:24px;top:253px">Pineapple Hawaiian Cole Slaw</div><div class="price" style="left:336px;top:252px">$&amp;.&amp;&amp;</div>
  <div class="dish" style="left:24px;top:286px">Fresh Watermelon Wedges</div><div class="price" style="left:336px;top:285px">$&amp;.&amp;&amp;</div>
  <div class="dish" style="left:24px;top:315px">Fresh Fruit and Melon Platter</div><div class="price" style="left:336px;top:314px">$&amp;.&amp;&amp;</div>

  <div class="section-rule" style="left:0;top:361px;width:440px"></div>
  <h2 class="section-badge" style="left:110px;top:343px;width:210px">Signature Soups</h2>
  <p class="section-note" style="left:74px;top:391px;font-size:13.5px">all Served with fresh Baked Sourdough Baguettes</p>

  <div class="dish" style="left:24px;top:417px">Cream of Crab Soup</div>
  <p class="desc" style="left:24px;top:436px;width:400px">Rich and Creamy Maryland Classic finished with Sherry Wine.</p>
  <div class="price" style="left:337px;top:452px">$&amp;.&amp;&amp;</div>

  <div class="dish" style="left:24px;top:464px">Maryland Hard Crab Soup</div>
  <p class="desc" style="left:24px;top:485px;width:400px">Maryland’s traditional Crab Soup, loaded with fresh Vegetables and Lump Crab Meat.</p>
  <div class="price" style="left:337px;top:500px">$&amp;.&amp;&amp;</div>

  <div class="dish" style="left:24px;top:523px">Seafood Bisque</div>
  <p class="desc" style="left:24px;top:544px;width:400px">Scallops, Crab, Salmon, and Lobster in a Rich and Creamy Broth, Spiked with Brandy.</p>
  <div class="price" style="left:337px;top:560px">$&amp;.&amp;&amp;</div>

  <div class="dish" style="left:24px;top:584px">Chef Marco’s Creamy Tortilla Soup</div>
  <p class="desc" style="left:24px;top:605px;width:400px">An HFC favorite. Delicious with just a hint of spice, served with Crispy Tortilla Strips, Great Vegetarian Soup! Want Chicken, no problem.</p>
  <div class="price" style="left:337px;top:636px">$&amp;.&amp;&amp;</div>

  <p class="terms">All Prices are per Person, with a 10 person minimum order per item chosen.<br>Local Products used when available and in season</p>

  <footer class="contact">
    <span class="contact__call">CALL OR EMAIL US TODAY:</span>
    <span class="contact__phone">
      <svg width="24" height="20" viewBox="0 0 24 20" aria-hidden="true"><path d="M2,7 C2,2 22,2 22,7 L22,9 L17,9 L17,6 L7,6 L7,9 L2,9 Z M6,10 L18,10 L21,18 L3,18 Z" fill="#1c1a17"/><circle cx="12" cy="14" r="2.2" fill="#f07a22"/></svg>
      410-555-0148
    </span>
    <address class="contact__address" style="font-style:normal">214 Orchard Way<br>Millbrook, MD 20999<br>www.harborfieldcaterers.com</address>
  </footer>

  <div class="brand" style="left:434px">
    <span class="brand__dot"></span>
    <span class="brand__name">Harbor Field<br>Caterers</span>
  </div>
</section>

</body>
</html>
```